Business Card (double-sided) and Stationary Design for dental office

1) Business Card Design: We need a business card design for a dental specialty office.
Texts should contain:
The name of our office "Brindle Oaks Orthodontics"
Tagline: "Specialist in Orthodontic and Maxillofacial Orthopedics"
Tag line: "Creating "Tolvering" smiles for Children and Adults"
Doctor name: "Doctor Name"
Office Address:
"123 Street Name
City, State Zip code"
Office email address: office@brindleoaksortho.com
Website: www.brindleoaksortho.com

We will provide the full office address once the design is selected
Theme: beach, paradise, coastal, wave
We would like to have some creativity in design. Some acceptable ideas: front page: logo and office name. Back page: more detail information, and map to office in form of an island. Please see sample from our other location, but you DON'T HAVE TO USE OR COPY THE SAME CONCEPT.

IF POSSIBLE, PLEASE SUBMIT AT LEAST TWO CONCEPTS: ONE WITH THE BACK LOOKING SIMILAR TO WHAT IS IN THE SAMPLE, AND ONE DIFFERENT.

Color: designer to choose. We have different shade of blues and sand color in our office. Please see logo.

2) Please also design a matching set of stationary that compliment the business card and our logo.

Target Market(s)

Dental

Contact Information for Business Card

See descriptions

Font styles to use
Other font styles liked:
• Matching texts in logo

Colors
0054AA
0677BA
7BADD7
CADEEF
E8F1F8
0094D4
00A9DD
6FCCEA
C7EBF8
E9F6FB
00AB8E
00BBA5
67D7C9
C6EFE9
E9F9F6

Requirements
Must have
• Double-sided
Nice to have
• Beach coastal theme
Should not have
• Any shape or drawing of of tooth or teeth. We don’t need these. You don't necessarily have to just cut and paste the logo art and text as a whole, you have the liberty to rearrange the text.

```html
<!DOCTYPE html>
<html lang="en">
<head>
<meta charset="utf-8">
<title>Brindle Oaks Orthodontics – Stationery Set</title>
<link href="https://fonts.googleapis.com/css2?family=Montserrat:wght@300;400;500&family=Ubuntu:wght@500;700&display=swap" rel="stylesheet">
<style>
  :root{
    --bg:#959293;
    --paper:#f4f3f3;
    --teal:#3a8ea5;
    --teal-soft:#6cc3bd;
    --mark-faint:#d9e4e9;
    --ink:#4a4a4a;
    --ink-soft:#6d6d6d;
    --sky:#57b8e6;
    --sea:#2f9ed0;
    --sand:#e9c37a;
    --tag-red:#7a1d12;
  }
  *{margin:0;padding:0;box-sizing:border-box}
  html,body{width:1200px;height:826px;overflow:hidden}
  body{background:var(--bg);position:relative;font-family:"Montserrat",sans-serif;color:var(--ink)}
  .sheet{position:absolute;background:var(--paper);overflow:hidden}
  .brand-name{font-family:"Ubuntu",sans-serif;font-weight:500;color:var(--teal);white-space:nowrap}
  .brand-sub{font-family:"Ubuntu",sans-serif;font-weight:500;color:var(--teal-soft);letter-spacing:.6px;white-space:nowrap}
  .brand-dot{border-radius:50%;background:var(--teal)}
  .faint-disc{position:absolute;border-radius:50%;background:var(--mark-faint);opacity:.75}
  .bottom-band{position:absolute;left:0;right:0;bottom:0;height:7px;background:var(--teal)}

  /* letterhead */
  .letterhead{left:60px;top:111px;width:461px;height:646px}
  .letterhead .brand{position:absolute;left:36px;top:44px;text-align:center;width:150px}
  .letterhead .brand-dot{width:46px;height:46px;margin:0 auto 6px}
  .letterhead .brand-name{font-size:14px;letter-spacing:-.2px}
  .letterhead .brand-sub{font-size:5.2px}
  .letterhead .faint-disc{left:130px;top:202px;width:212px;height:212px}
  .contact{position:absolute;left:289px;top:71px;font-size:8.6px;line-height:11px;color:var(--ink-soft);font-weight:300}
  .contact .gap{height:6px}
  .contact .row{display:flex;align-items:center;gap:5px;color:var(--teal);font-weight:400}
  .contact svg{width:7px;height:7px;fill:var(--teal)}
  .letter{position:absolute;left:41px;top:188px;width:381px;color:var(--ink-soft)}
  .salutation{font-size:12px;font-weight:400;margin-bottom:14px;color:var(--ink)}
  .letter p{font-size:6.2px;line-height:9.8px;font-weight:300;margin-bottom:8.5px;text-align:justify}
  .sign-off{font-size:6.5px;font-weight:300;margin-top:21px}

  /* business card front */
  .card-front{left:550px;top:120px;width:288px;height:164px}
  .card-front .big-disc{position:absolute;left:126px;top:-8px;width:190px;height:190px;border-radius:50%;background:var(--teal)}
  .card-front .person{position:absolute;left:18px;top:84px;font-family:"Ubuntu",sans-serif;font-weight:500;font-size:11.5px;color:var(--teal)}
  .card-front .details{position:absolute;left:18px;top:107px;font-size:6px;line-height:7.6px;color:var(--ink)}
  .card-front .details div{display:flex;gap:4px;align-items:flex-start}
  .card-front .details svg{width:5px;height:5px;fill:var(--teal);margin-top:1px;flex:none}

  /* business card back */
  .card-back{left:862px;top:120px;width:288px;height:164px}
  .card-back .scene{position:absolute;inset:0;background:linear-gradient(180deg,var(--sky) 0%,#bfe3f4 38%,var(--sea) 48%,#7fd0e8 58%,var(--sand) 66%,#d7a85a 100%)}
  .card-back .brand{position:absolute;left:0;right:0;top:18px;text-align:center}
  .card-back .brand-dot{width:28px;height:28px;margin:0 auto 3px;background:#4a2c24}
  .card-back .brand-name{font-size:9px;color:#4a2c24}
  .appt{position:absolute;left:2px;top:76px;width:192px;height:48px;background:rgba(255,255,255,.82);border-radius:4px;padding:6px 6px;font-size:6px;color:#222}
  .appt h2{font-size:6.3px;font-weight:500;margin-bottom:6px}
  .appt .line{display:flex;align-items:flex-end;margin-bottom:4px}
  .appt .line span{flex:1;border-bottom:1px dotted #555;margin:0 2px 1px}
  .taglines{position:absolute;left:18px;top:137px;font-size:6px;font-weight:500;color:var(--tag-red);line-height:8.5px}
  .taglines em{font-style:italic;font-weight:500}

  /* envelopes */
  .envelope-back{left:602px;top:337px;width:529px;height:240px;background:#f6f5f5}
  .envelope-back .flap{position:absolute;left:0;top:0;width:529px;height:76px}
  .envelope-back .flap-mark{position:absolute;left:230px;top:15px;width:44px;height:44px;border-radius:50%;border:4px solid #fff}
  .envelope-front{left:565px;top:511px;width:530px;height:242px}
  .envelope-front .brand{position:absolute;left:27px;top:27px;width:140px;text-align:center}
  .envelope-front .brand-dot{width:46px;height:46px;margin:0 auto 6px}
  .envelope-front .brand-name{font-size:13px;letter-spacing:-.2px}
  .envelope-front .brand-sub{font-size:5px}
  .envelope-front .address{position:absolute;left:28px;top:100px;font-size:9px;line-height:11.5px;color:var(--ink-soft);font-weight:300;letter-spacing:.3px}
  .envelope-front .faint-disc{left:313px;top:30px;width:184px;height:184px}
</style>
</head>
<body>

<section class="sheet letterhead">
  <div class="faint-disc"></div>
  <div class="brand">
    <div class="brand-dot"></div>
    <div class="brand-name">Brindle Oaks Orthodontics</div>
    <div class="brand-sub">Pediatric Dentistry &amp; Orthodontics</div>
  </div>
  <div class="contact">
    <div>123 Street Name</div>
    <div>City, State Zip code</div>
    <div class="gap"></div>
    <div class="row"><svg viewBox="0 0 10 10"><path d="M2 0l2 2-1 2 3 3 2-1 2 2-2 2C4 10 0 6 0 2z"/></svg>555-014-2736</div>
    <div class="row"><svg viewBox="0 0 10 10"><rect y="2" width="10" height="6"/></svg>office@brindleoaksortho.com</div>
    <div class="row"><svg viewBox="0 0 10 10"><circle cx="5" cy="5" r="5"/></svg>www.brindleoaksortho.com</div>
  </div>
  <div class="letter">
    <div class="salutation">Dear Mr. Harper,</div>
    <p>Lorem ipsum dolor sit amet, consectetur adipiscing elit. Donec orci purus, luctus vitae dignissim eu, iaculis sed purus. Vivamus faucibus, ipsum nec aliquet viverra, leo mauris condimentum ligula, sit amet sagittis enim ligula quis arcu. Nam egestas tortor id nisi porttitor mattis. In tortor ante, ultricies in suscipit a, tempus non massa. Vivamus et auctor mi. Fusce vel massa nulla. Phasellus nec eros mauris, et scelerisque orci.</p>
    <p>Donec malesuada orci vitae nulla accumsan porta a id massa. Quisque accumsan iaculis magna sit amet fringilla. Maecenas consequat, magna eget tincidunt semper, odio nibh rutrum mi, id feugiat ante nisi eu risus. Vestibulum nunc orci, rhoncus a placerat in, ultricies in mi. Cras mattis varius eros, vel fringilla nisi suscipit eget. Quisque scelerisque sagittis nulla at porttitor.</p>
    <p>Sed id augue vitae urna euismod commodo aliquet a quam. Pellentesque arcu velit, cursus et malesuada ut, consequat et diam. Nullam erat sem, rhoncus id ullamcorper vitae, rhoncus et arcu. In ultricies ultricies nulla, ut rutrum nisl iaculis at. Donec eu magna a metus ornare faucibus. Fusce aliquet faucibus ultricies. Morbi semper, est id tincidunt gravida, sem arcu adipiscing lacus, ac bibendum nulla leo eu purus. Quisque nec diam sed risus consectetur accumsan quis quis nibh. Vestibulum id purus lorem.</p>
    <p>It is a long established fact that a reader will be distracted by the readable content of a page when looking at its layout. The point of using Lorem Ipsum is that it has a more-or-less normal distribution of letters, as opposed to using 'Content here, content here', making it look like readable English. Many desktop publishing packages</p>
    <div class="sign-off">Sincerely,</div>
  </div>
  <div class="bottom-band"></div>
</section>

<section class="sheet card-front">
  <div class="big-disc"></div>
  <div class="person">Daniel Harper</div>
  <div class="details">
    <div><svg viewBox="0 0 10 10"><circle cx="5" cy="4" r="4"/><path d="M2 6l3 4 3-4z"/></svg><span>123 Street Name<br>City, State Zip code</span></div>
    <div><svg viewBox="0 0 10 10"><path d="M2 0l2 2-1 2 3 3 2-1 2 2-2 2C4 10 0 6 0 2z"/></svg>555-014-2736</div>
    <div><svg viewBox="0 0 10 10"><rect y="2" width="10" height="6"/></svg>office@brindleoaksortho.com</div>
    <div><svg viewBox="0 0 10 10"><circle cx="5" cy="5" r="5"/></svg>brindleoaksortho.com</div>
  </div>
</section>

<section class="sheet card-back">
  <div class="scene" role="img" aria-label="Illustrated tropical beach with palm trees, a rocky island, sea and a small road map to the office"></div>
  <div class="brand">
    <div class="brand-dot"></div>
    <div class="brand-name">Brindle Oaks Orthodontics</div>
  </div>
  <div class="appt">
    <h2>SEE YOU AT YOUR NEXT APPOINTMENT!</h2>
    <div class="line">For<span></span></div>
    <div class="line">Date<span></span>Time<span></span></div>
  </div>
  <div class="taglines">
    <div>Specialist in Orthodontic &amp; Maxillofacial Orthopedics</div>
    <div><em>Creating "Tolvering" smiles for Children &amp; Adults</em></div>
  </div>
</section>

<section class="sheet envelope-back">
  <svg class="flap" viewBox="0 0 529 76" preserveAspectRatio="none"><path d="M0 0H529V50Q529 76 503 76H26Q0 76 0 50Z" fill="#3a8ea5"/></svg>
  <div class="flap-mark"></div>
</section>

<section class="sheet envelope-front">
  <div class="faint-disc"></div>
  <div class="brand">
    <div class="brand-dot"></div>
    <div class="brand-name">Brindle Oaks Orthodontics</div>
    <div class="brand-sub">Pediatric Dentistry &amp; Orthodontics</div>
  </div>
  <div class="address">123 Street Name<br>City, State Zip code</div>
  <div class="bottom-band"></div>
</section>

</body>
</html>
```